Manifesto

I want a manifesto with the following five manifestos for our Not for Profit

- We are a For-purpose organisation
- Every service we offer is free
- Every product we sell funds our services
- Every financial transaction is transparent
- Our service is for the greater good
- Our purpose is always to serve the people
- We are a for purpose organisation

Its to go with this website logo/look/feel www.brightharbour.co.nz

Two attachments:

1. I quite like this look/feel of a manifesto (see attached), I want something clean, professional but I also quite like either Retro modern look feel also like a fresh, and uplifting as its for sick people coming to see us and our funds where anyone buys a product are used for helping those who are sick with healing......so needs something conveyed that is fresh, uplifing yet professional.
2. This attachment is how I wrote this down when inspired of how I wanted Bright Harbour to operate. This is our values chart. It has to say

Also check out our website for our logo, look etc.. it doesnt have to be the same but red somewhere would link back to logo. www.brightharbour.co.nz .

Industry/Entity Type

Financial

```html
<!DOCTYPE html>
<html lang="en">
<head>
<meta charset="utf-8">
<title>Our Manifesto — Bright Harbour</title>
<link rel="stylesheet" href="https://fonts.googleapis.com/css2?family=Archivo:wdth,wght@62..125,100..900&family=Rammetto+One&display=swap">
<style>
  :root {
    --paper: #ecdfc8;
    --paper-deep: #dcc7a6;
    --paper-shade: #d2b995;
    --ink: #2a211c;
    --ink-soft: #4a3e35;
    --harbour-red: #c62232;
    --display: "Rammetto One", "Archivo", sans-serif;
    --text: "Archivo", sans-serif;
  }
  * { margin: 0; padding: 0; box-sizing: border-box; }
  html, body { width: 1200px; height: 1110px; overflow: hidden; background: var(--paper); }
  .manifesto {
    position: relative;
    width: 1200px;
    height: 1110px;
    overflow: hidden;
    color: var(--ink);
    font-family: var(--text);
    font-weight: 900;
    font-stretch: 118%;
    background:
      radial-gradient(ellipse 260px 200px at 1140px 980px, var(--paper-shade), transparent 70%),
      radial-gradient(ellipse 220px 160px at 1080px 140px, var(--paper-deep), transparent 70%),
      radial-gradient(ellipse 200px 160px at 40px 500px, var(--paper-deep), transparent 70%),
      radial-gradient(ellipse 180px 120px at 150px 40px, var(--paper-deep), transparent 70%),
      var(--paper);
  }
  .line {
    position: absolute;
    display: block;
    white-space: nowrap;
    text-transform: uppercase;
    line-height: 1;
    font-weight: 900;
    text-shadow: 2px 2px 0 var(--paper), 4px 4px 0 var(--ink-soft);
  }
  .justified { text-align: justify; text-align-last: justify; }

  .title-our {
    left: 341px; top: 47px; width: 510px;
    font-family: var(--display);
    font-weight: 400;
    font-size: 184px;
    letter-spacing: 2px;
    text-shadow: 4px 4px 0 var(--paper), 8px 8px 0 var(--ink-soft);
  }
  .title-manifesto { left: 345px; top: 225px; width: 503px; font-size: 64px; }

  .rule {
    position: absolute; left: 126px; width: 932px; height: 3px;
    background: var(--ink);
  }
  .rule--top { top: 316px; }
  .rule--bottom { top: 999px; }

  .v1a { left: 134px; top: 363px; width: 441px; font-size: 29px; }
  .v1b { left: 134px; top: 394px; width: 438px; font-size: 48px; }
  .v2a { left: 137px; top: 485px; width: 447px; font-size: 46px; }
  .v2b { left: 134px; top: 531px; width: 450px; font-size: 26px; }
  .v3a { left: 718px; top: 360px; width: 388px; font-size: 44px; }
  .v3b { left: 718px; top: 414px; width: 388px; font-size: 35px; }
  .v4a { left: 718px; top: 491px; width: 388px; font-size: 20px; }
  .v4b { left: 718px; top: 515px; width: 396px; font-size: 42px; }
  .v5  { left: 137px; top: 608px; width: 974px; font-size: 42px; }
  .v6a { left: 134px; top: 689px; width: 970px; font-size: 62px; }
  .v6b { left: 134px; top: 757px; width: 972px; font-size: 64px; }
  .v7a { left: 134px; top: 859px; width: 424px; font-size: 76px; }
  .v7b { left: 577px; top: 883px; width: 529px; font-size: 33px; }

  .brand {
    position: absolute; left: 0; top: 1016px; width: 1200px;
    display: flex; flex-direction: column; align-items: center;
  }
  .brand-name {
    display: flex; align-items: center; gap: 10px;
    color: var(--harbour-red);
    font-size: 32px;
    line-height: 1;
  }
  .brand-dot { width: 22px; height: 22px; border-radius: 50%; background: var(--harbour-red); }
  .brand-tagline {
    margin-top: 10px;
    color: var(--ink-soft);
    font-size: 12px;
    letter-spacing: 1px;
    text-transform: uppercase;
  }
</style>
</head>
<body>
<main class="manifesto">
  <h1>
    <span class="line title-our">Our</span>
    <span class="line justified title-manifesto">Manifesto</span>
  </h1>
  <div class="rule rule--top"></div>

  <p class="line justified v1a">We are a for-purpose</p>
  <p class="line justified v1b">Organisation</p>

  <p class="line justified v2a">Every product</p>
  <p class="line justified v2b">We sell funds our services</p>

  <p class="line justified v3a">Every service</p>
  <p class="line justified v3b">We offer is free</p>

  <p class="line justified v4a">Every financial transaction</p>
  <p class="line justified v4b">Is transparent</p>

  <p class="line justified v5">Our service is for the greater good</p>

  <p class="line justified v6a">Our purpose is always</p>
  <p class="line justified v6b">To serve the people</p>

  <p class="line justified v7a">We are a</p>
  <p class="line justified v7b">For purpose organisation</p>

  <div class="rule rule--bottom"></div>

  <footer class="brand">
    <div class="brand-name"><span class="brand-dot"></span>Bright Harbour</div>
    <div class="brand-tagline">Care • Healing • Hope</div>
  </footer>
</main>
</body>
</html>
```